Hartwell Estates Business Cards

I would like a business card that includes myself and my partner.
Includes: Logo, office #, email, website, our names, our numbers and possibly the address. I would also like the logo to be embossed and the card to be horizontal.
There is a photo of our yard signs to give you an idea of the colors of our business.

Target Market(s)

Everyone in real estate market.
We are in a rural area. Our clientele are from all socioeconomic backgrounds.

Industry/Entity Type

Real Estate Agent

Contact Information for Business Card

Company Name: Hartwell Estates
Our Names, Titles & Cell #'s : Dana Pembrook-Broker (555).317.6624, Marla Pembrook-Realtor (555).609.1385
Office #: (555).240.3918
Website: hartwellestates-demo.com
Joint Email: pembrook@hartwellestates-demo.com
Office Address: 418B W. Calloway Ave.
Millbrook, LA. 70913

Font styles to use
Serif

Requirements
Must have
• HORIZONTAL, Logo, Myself and my partners names, Our cell #'s, our office #, our website, our email address
Nice to have
• Embossed logo, office address, our titles.

```html
<!DOCTYPE html>
<html lang="en">
<head>
<meta charset="utf-8">
<title>Hartwell Estates Business Cards</title>
<link rel="stylesheet" href="https://fonts.googleapis.com/css2?family=Crimson+Pro:wght@600&family=Source+Sans+3:wght@400;600&display=swap">
<style>
  :root {
    --backdrop: #d9d9d9;
    --paper: #ffffff;
    --plum: #4a2262;
    --plum-text: #45195c;
    --ink: #2b2b2b;
    --rule: #b9a6c6;
  }
  * { margin: 0; padding: 0; box-sizing: border-box; }
  html, body { width: 1200px; height: 900px; overflow: hidden; }
  body {
    background: var(--backdrop);
    font-family: "Source Sans 3", "Myriad Pro", Arial, sans-serif;
    color: var(--ink);
    position: relative;
  }
  .card {
    position: absolute;
    width: 478px;
    height: 295px;
    top: 275px;
    box-shadow: 3px 4px 6px rgba(0,0,0,0.35);
  }
  .card-front {
    left: 116px;
    background: var(--paper);
    border-radius: 0 46px 0 46px;
  }
  .card-back {
    left: 622px;
    background: var(--plum);
    border-radius: 46px 0 46px 0;
  }
  .brand {
    position: absolute;
    display: flex;
    align-items: center;
    gap: 14px;
    font-family: "Crimson Pro", Georgia, serif;
    font-weight: 600;
    white-space: nowrap;
  }
  .brand-mark {
    border-radius: 50%;
    flex: none;
  }
  .card-front .brand {
    left: 0; right: 0; top: 50px;
    justify-content: center;
    color: var(--plum-text);
    font-size: 40px;
  }
  .card-front .brand-mark { width: 30px; height: 30px; background: var(--plum-text); }
  .card-back .brand {
    left: 0; right: 0; top: 118px;
    justify-content: center;
    color: var(--paper);
    font-size: 44px;
  }
  .card-back .brand-mark { width: 32px; height: 32px; background: var(--paper); }

  .agent {
    position: absolute;
    top: 136px;
    width: 200px;
  }
  .agent-left { right: 255px; text-align: right; }
  .agent-right { left: 247px; text-align: left; }
  .agent-name {
    font-weight: 600;
    font-size: 16.5px;
    color: var(--plum-text);
    line-height: 20px;
  }
  .agent-title { font-size: 13px; line-height: 16px; }
  .agent-phone {
    font-size: 13.5px;
    line-height: 16px;
    margin-top: 5px;
    display: flex;
    align-items: center;
    gap: 5px;
  }
  .agent-left .agent-phone { justify-content: flex-end; }
  .phone-icon { width: 10px; height: 10px; fill: var(--plum-text); }

  .office {
    position: absolute;
    left: 0; right: 0;
    text-align: center;
    font-size: 13.5px;
    line-height: 17px;
  }
  .office-line { top: 206px; }
  .office-line .office-phone { margin-right: 20px; }
  .office-web { top: 223px; }

  .address-row {
    position: absolute;
    left: 10px; right: 0; top: 252px;
    display: flex;
    align-items: center;
    gap: 10px;
    font-size: 13px;
  }
  .address-row .rule {
    flex: 1;
    height: 1px;
    background: var(--rule);
  }
</style>
</head>
<body>

  <section class="card card-front" aria-label="Business card front">
    <div class="brand">
      <span class="brand-mark"></span>
      <span class="brand-name">Hartwell Estates</span>
    </div>

    <div class="agent agent-left">
      <p class="agent-name">Dana Pembrook</p>
      <p class="agent-title">Broker</p>
      <p class="agent-phone">(555).317.6624
        <svg class="phone-icon" viewBox="0 0 24 24" aria-hidden="true"><path d="M6.6 10.8c1.4 2.8 3.8 5.1 6.6 6.6l2.2-2.2c.3-.3.7-.4 1-.2 1.1.4 2.300.6 3.6.6.6 0 1 .4 1 1V20c0 .6-.4 1-1 1C10.6 21 3 13.4 3 4c0-.6.4-1 1-1h3.5c.6 0 1 .4 1 1 0 1.3.2 2.5.6 3.6.1.3 0 .7-.2 1z"/></svg>
      </p>
    </div>

    <div class="agent agent-right">
      <p class="agent-name">Marla Pembrook</p>
      <p class="agent-title">Realtor</p>
      <p class="agent-phone">
        <svg class="phone-icon" viewBox="0 0 24 24" aria-hidden="true"><path d="M6.6 10.8c1.4 2.8 3.8 5.1 6.6 6.6l2.2-2.2c.3-.3.7-.4 1-.2 1.1.4 2.3.6 3.6.6.6 0 1 .4 1 1V20c0 .6-.4 1-1 1C10.6 21 3 13.4 3 4c0-.6.4-1 1-1h3.5c.6 0 1 .4 1 1 0 1.3.2 2.5.6 3.6.1.3 0 .7-.2 1z"/></svg>
        (555).609.1385</p>
    </div>

    <p class="office office-line"><span class="office-phone">(555).240.3918</span><span class="office-email">pembrook@hartwellestates-demo.com</span></p>
    <p class="office office-web">hartwellestates-demo.com</p>

    <div class="address-row">
      <span class="rule"></span>
      <span class="address">418B W. Calloway Ave. Millbrook, LA. 70913</span>
      <span class="rule"></span>
    </div>
  </section>

  <section class="card card-back" aria-label="Business card back">
    <div class="brand">
      <span class="brand-mark"></span>
      <span class="brand-name">Hartwell Estates</span>
    </div>
  </section>

</body>
</html>
```